Initial website for sport tech startup

We are currently in the R&D phases of our new product. It’s a headband to prevent concussion in the soccer market initially.

We have 2 products, one that’s basic aimed at the youth market and the other more technology driven that’s aimed at the academies and professional market.

Initially the product will launch in the UK

Target Market(s)

Youth soccer players and parents in UK, Soccer Clubs, Federations.

Industry/Entity Type

Sporting Good

Coding

Coded - Design and coding required

Number of Pages Required

5+ page

Requirements
Must have
• Professional style that can be adapted and changed over the coming months.
Nice to have
• Ecommerce ability in the future.

```html
<!DOCTYPE html>
<html lang="en">
<head>
<meta charset="utf-8">
<title>Crestguard — Bringing Safety to the Sports Concussion Debate</title>
<link href="https://fonts.googleapis.com/css2?family=Lato:ital,wght@0,300;0,400;0,700;0,900;1,300;1,400&display=swap" rel="stylesheet">
<style>
:root{
  --navy:#1d3f73;
  --blue:#1a4f8f;
  --sky:#1b86c7;
  --ink:#222;
  --text:#555;
  --line:#c9ced6;
  --panel:#f1f1f1;
  --panel-mid:#e4e5e7;
  --white:#fff;
  --footer:#121212;
}
*{box-sizing:border-box;margin:0;padding:0}
html,body{width:1200px;height:5319px;overflow:hidden}
body{font-family:"Lato",sans-serif;color:var(--text);background:var(--white)}
.wrap{width:1022px;margin:0 auto;position:relative;height:100%}
section,header,footer{position:relative;width:1200px;overflow:hidden}
h2.section-title{font-weight:700;font-size:40px;color:var(--ink);text-align:center;letter-spacing:.5px}
.btn{display:inline-flex;align-items:center;gap:8px;border-radius:30px;font-weight:900;font-size:15px;text-transform:uppercase;padding:0 30px;height:54px;background:var(--blue);color:#fff}
.btn .dot{width:16px;height:16px;border-radius:50%;background:currentColor;position:relative}
.btn .dot::after{content:"";position:absolute;left:5px;top:4px;border-left:6px solid var(--blue);border-top:4px solid transparent;border-bottom:4px solid transparent}
.social{display:flex;gap:8px}
.social span{width:34px;height:34px;border:1px solid rgba(255,255,255,.7)}

.topbar{height:45px;background:var(--navy);color:#fff;font-size:15px}
.topbar .wrap{display:flex;align-items:center;justify-content:space-between}
.contact-line{display:flex;gap:22px;align-items:center}
.contact-line span{display:flex;align-items:center;gap:7px}
.contact-line b{font-weight:700}

.nav{height:79px;border-bottom:1px solid #e5e5e5}
.nav .wrap{display:flex;align-items:center;justify-content:space-between}
.brand{font-size:38px;font-weight:900;color:var(--navy);letter-spacing:1px}
.menu{display:flex;gap:24px;font-size:14px;font-weight:700;color:var(--ink);text-transform:uppercase}
.menu .active{color:var(--navy);border-bottom:2px solid var(--navy);padding-bottom:3px}

.hero{height:516px}
.hero-photo{position:absolute;inset:0;background:linear-gradient(180deg,#2a3b52 0%,#3f5a45 45%,#2d6a28 75%,#1f4a1b 100%)}
.hero-content{position:absolute;left:0;right:0;top:120px;text-align:center;color:#fff}
.hero-title{font-size:82px;font-weight:700;letter-spacing:4px;line-height:1}
.hero-text{width:820px;margin:24px auto 30px;font-size:18px;line-height:33px}

.features{height:675px}
.feature-row{position:absolute;top:97px;left:0;right:0;display:flex;justify-content:space-between;padding:0 4px}
.feature{width:184px;height:184px;border-radius:50%;border:6px solid var(--navy);border-bottom-color:transparent;display:flex;flex-direction:column;align-items:center;justify-content:center;gap:8px;text-align:center;font-size:17px;color:var(--ink);line-height:1.3}
.feature svg{width:62px;height:62px}
.intro{position:absolute;left:43px;top:322px;width:410px}
.intro h3{font-size:16px;font-weight:700;color:var(--sky);line-height:27px;text-transform:uppercase;margin-bottom:20px}
.intro p{font-size:16px;line-height:27px;margin-bottom:26px}
.intro .btn{height:58px}
.intro-photo{position:absolute;left:592px;top:329px;width:387px;height:246px;background:linear-gradient(160deg,#6c8f3c,#a7c26a 45%,#c48fc0 60%,#5e7b30)}

.about{height:537px;background:linear-gradient(180deg,#0f3a72 0%,#1c5797 50%,#0e3768 100%);color:#fff;text-align:center}
.about h2{font-size:42px;font-weight:700;margin-top:113px}
.about p{width:795px;margin:22px auto 30px;font-size:16px;line-height:32px}
.about .btn{background:#fff;color:var(--navy);height:58px}
.about .btn .dot::after{border-left-color:#fff}

.testimonials{height:508px}
.testimonials h2{margin-top:88px}
.cards{position:absolute;left:89px;top:217px;display:flex;gap:22px}
.t-card{width:326px;height:250px;background:#fff;box-shadow:0 4px 16px rgba(0,0,0,.14);text-align:center;padding-top:78px;position:relative}
.avatar{position:absolute;left:50%;top:-50px;margin-left:-50px;width:100px;height:100px;border-radius:50%;border:4px solid #fff;background:linear-gradient(135deg,#b9c1cc,#6d7885)}
.t-card h4{font-size:16px;color:var(--ink);font-weight:700;margin-bottom:22px}
.t-card p{font-style:italic;font-weight:300;font-size:13.5px;line-height:24px;color:#777;padding:0 22px}
.arrow{position:absolute;width:14px;height:14px;border-left:3px solid #555;border-bottom:3px solid #555}
.arrow.left{transform:rotate(45deg)}
.arrow.right{transform:rotate(-135deg)}

.touch{height:552px}
.touch-art{position:absolute;left:0;top:0;width:553px;height:552px;background:radial-gradient(ellipse at 50% 50%,var(--panel-mid) 0%,var(--panel) 70%)}
.touch-form{position:absolute;left:600px;top:48px;width:510px}
.touch-form h2{font-size:40px;font-weight:700;color:var(--ink);margin-bottom:26px}
.field{height:50px;border:1px solid var(--line);margin-bottom:13px;padding:0 20px;display:flex;align-items:center;font-size:15px;color:#999}
.field.msg{height:132px;align-items:flex-start;padding-top:15px}
.touch-form .btn{height:50px;padding:0 45px;margin-top:2px}

.videos{height:499px}
.videos h2{margin-top:86px}
.video-row{position:absolute;left:89px;top:168px;display:flex;gap:22px}
.video{width:326px;height:233px;position:relative}
.video::after{content:"";position:absolute;left:148px;top:97px;border-left:32px solid #fff;border-top:19px solid transparent;border-bottom:19px solid transparent}
.v1{background:linear-gradient(180deg,#151a22,#3a4d5a 70%,#24311f)}
.v2{background:linear-gradient(180deg,#6f8d5a,#4d7a32 40%,#3f6b2a)}
.v3{background:linear-gradient(180deg,#9bb4c9,#4b7d38 55%,#3a6a2a)}

.team{height:498px;background:var(--sky);color:#fff;text-align:center}
.team h2{color:#fff;margin-top:88px}
.members{display:flex;justify-content:center;gap:93px;margin-top:24px}
.member{width:190px}
.member .photo{width:190px;height:190px;border-radius:50%;border:3px solid #fff;background:linear-gradient(160deg,#d4dbe4,#8b98a8)}
.member h4{font-size:17px;font-weight:700;text-transform:uppercase;margin-top:14px}
.member p{font-size:17px;font-weight:700;margin-top:4px}

.blog{height:630px}
.blog h2{margin-top:87px}
.posts{position:absolute;left:89px;top:167px;display:flex;gap:22px}
.post{width:326px}
.post .thumb{height:197px}
.b1{background:linear-gradient(180deg,#3e6f2a,#e3d23a 55%,#2f5e22)}
.b2{background:linear-gradient(180deg,#c9d1dc,#5e8146 60%,#3d6a2c)}
.b3{background:linear-gradient(180deg,#1d2433,#4b5a6a 55%,#2e4f25)}
.share{display:flex;gap:6px;margin:20px 0 10px 8px}
.share span{width:16px;height:16px;border:1px solid #bbb}
.post h4{font-size:16px;font-weight:400;color:var(--ink);margin-bottom:8px}
.post p{font-size:13.5px;line-height:24px;color:#777;margin-bottom:10px}
.meta{font-size:12.5px;color:var(--navy);display:flex;gap:14px}

.map{height:448px}
.map-fill{position:absolute;inset:0;background:linear-gradient(135deg,#eceeea,#e2e6e0 50%,#eceae4)}
.map-card{position:absolute;left:475px;top:270px;width:250px;height:102px;background:#fff;box-shadow:0 2px 8px rgba(0,0,0,.2);text-align:center;font-size:15px;line-height:23px;color:#444;padding-top:16px}
.pin{position:absolute;left:597px;top:185px}

.footer{height:332px;background:var(--footer);color:#fff;text-align:center}
.footer .brand{color:#2f67b3;display:block;padding-top:62px;font-size:46px}
.footer .social{justify-content:center;margin-top:112px}
.footer .social span{width:38px;height:38px}
.copy{font-size:12.5px;margin-top:34px}
</style>
</head>
<body>

<header class="topbar">
  <div class="wrap">
    <div class="contact-line">
      <span><svg width="11" height="15" viewBox="0 0 11 15"><path d="M5.5 0C2.5 0 0 2.4 0 5.4 0 9.5 5.5 15 5.5 15S11 9.5 11 5.4C11 2.4 8.5 0 5.5 0zm0 7.5a2 2 0 110-4 2 2 0 010 4z" fill="#fff"/></svg>1420 Harlow Lane, Suite B, Austin, TX 78701</span>
      <span><svg width="14" height="14" viewBox="0 0 14 14"><path d="M3 0l3 3-2 2c1 2 3 4 5 5l2-2 3 3-2 3C6 14 0 8 0 2z" fill="#fff"/></svg><b>+44 20 7946 0321</b></span>
      <span><svg width="15" height="11" viewBox="0 0 15 11"><rect width="15" height="11" fill="#fff"/><path d="M0 0l7.5 6L15 0" stroke="#1d3f73" fill="none"/></svg>hello@crestguard.com</span>
    </div>
    <div class="social"><span></span><span></span><span></span><span></span><span></span></div>
  </div>
</header>

<header class="nav">
  <div class="wrap">
    <div class="brand">CRESTGUARD</div>
    <nav class="menu">
      <span class="active">Home</span><span>About Us</span><span>What We Do</span><span>Our Mission</span><span>Team</span><span>Product</span><span>Blog</span><span>Contact Us</span>
    </nav>
  </div>
</header>

<section class="hero">
  <div class="hero-photo" role="img" aria-label="Soccer players competing for the ball in a floodlit stadium"></div>
  <div class="hero-content">
    <div class="hero-title">CRESTGUARD</div>
    <p class="hero-text">Lorem ipsum dolor sit amet, consectetur adipiscing elit, sed do eiusmod tempor incididunt ut labore et dolore magna aliqua. Ut enim ad minim veniam</p>
    <span class="btn">Get More Info <i class="dot"></i></span>
  </div>
</section>

<section class="features">
  <div class="wrap">
    <div class="feature-row">
      <div class="feature">
        <svg viewBox="0 0 62 62" fill="none" stroke="#1b86c7" stroke-width="3"><circle cx="28" cy="34" r="22"/><circle cx="28" cy="34" r="13"/><circle cx="28" cy="34" r="4"/><path d="M28 34L52 10M46 10h6v6"/></svg>
        Our Mission</div>
      <div class="feature">
        <svg viewBox="0 0 62 62" fill="none" stroke="#1b86c7" stroke-width="3"><path d="M12 6v50M12 14h30l6 5-6 5H12M12 32h24l6 5-6 5H12"/></svg>
        Crestguard<br>Approach</div>
      <div class="feature">
        <svg viewBox="0 0 62 62" fill="none" stroke="#1b86c7" stroke-width="3"><path d="M6 40C6 24 18 18 31 18s25 6 25 22z"/><path d="M14 34h34"/></svg>
        Product</div>
      <div class="feature">
        <svg viewBox="0 0 62 62" fill="none" stroke="#1b86c7" stroke-width="3"><rect x="6" y="14" width="50" height="36"/><path d="M14 42l10-10 8 6 14-16"/></svg>
        Market Today</div>
    </div>
    <div class="intro">
      <h3>Crestguard – Bringing Safety to the Sports Concussion Debate</h3>
      <p>Crestguard is designing and developing head protection products to reduce the likelihood of concussion when playing sports. Exploring and understanding medical insights, material...</p>
      <span class="btn">Read More <i class="dot"></i></span>
    </div>
    <div class="intro-photo" role="img" aria-label="Injured soccer player lying on the pitch holding his head"></div>
  </div>
</section>

<section class="about">
  <h2>ABOUT US</h2>
  <p>Lorem ipsum dolor sit amet, consectetur adipiscing elit, sed do eiusmod tempor incididunt ut labore et dolore magna aliqua. Ut enim ad minim veniam, quis nostrud exercitation ullamco laboris nisi ut aliquip ex ea commodo consequat. Duis aute irure dolor in reprehenderit in voluptate velit esse cillum dolore eu fugiat nulla pariatur. Excepteur sint occaecat cupidatat non proident, sunt in culpa qui officia deserunt mollit anim id est laborum</p>
  <span class="btn">Read More <i class="dot"></i></span>
</section>

<section class="testimonials">
  <h2 class="section-title">TESTIMONIALS</h2>
  <i class="arrow left" style="left:42px;top:335px"></i>
  <i class="arrow right" style="right:42px;top:335px"></i>
  <div class="cards">
    <div class="t-card"><div class="avatar" role="img" aria-label="Portrait of Daniel K"></div><h4>Daniel K</h4><p>Lorem ipsum dolor sit amet, consectetur adipiscing elit, sed do eiusmod tempor unt ut labore et dolore magna aliqua. Ut enim ad minim veniam, quis nostrud exercitation mco</p></div>
    <div class="t-card"><div class="avatar" role="img" aria-label="Portrait of Maria S"></div><h4>Maria S</h4><p>Lorem ipsum dolor sit amet, consectetur adipiscing elit, sed do eiusmod tempor unt ut labore et dolore magna aliqua. Ut enim ad minim veniam, quis nostrud exercitation mco</p></div>
    <div class="t-card"><div class="avatar" role="img" aria-label="Portrait of Leo P"></div><h4>Leo P</h4><p>Lorem ipsum dolor sit amet, consectetur adipiscing elit, sed do eiusmod tempor unt ut labore et dolore magna aliqua. Ut enim ad minim veniam, quis nostrud exercitation mco</p></div>
  </div>
</section>

<section class="touch">
  <div class="touch-art" role="img" aria-label="Product illustration of the protective headband"></div>
  <div class="touch-form">
    <h2>GET IN TOUCH</h2>
    <div class="field">Name</div>
    <div class="field">Email</div>
    <div class="field">Phone No</div>
    <div class="field msg">Message</div>
    <span class="btn">Submit</span>
  </div>
</section>

<section class="videos">
  <h2 class="section-title">WATCH OUR VIDEOS</h2>
  <i class="arrow left" style="left:42px;top:277px"></i>
  <i class="arrow right" style="right:42px;top:277px"></i>
  <div class="video-row">
    <div class="video v1" role="img" aria-label="Video still of a player kicking a ball in a dark stadium"></div>
    <div class="video v2" role="img" aria-label="Video still of a ball on a grass pitch"></div>
    <div class="video v3" role="img" aria-label="Video still of players chasing the ball"></div>
  </div>
</section>

<section class="team">
  <h2 class="section-title">TEAM</h2>
  <div class="members">
    <div class="member"><div class="photo" role="img" aria-label="Portrait of Martin Hale"></div><h4>Martin Hale</h4><p>Founder / CEO</p></div>
    <div class="member"><div class="photo" role="img" aria-label="Portrait of Laura Penning"></div><h4>Laura Penning</h4><p>Co –Founder / COO</p></div>
    <div class="member"><div class="photo" role="img" aria-label="Portrait of Owen Carver"></div><h4>Owen Carver</h4><p>CCO</p></div>
  </div>
</section>

<section class="blog">
  <h2 class="section-title">BLOG</h2>
  <div class="posts">
    <article class="post"><div class="thumb b1" role="img" aria-label="Goalkeeper holding a ball on the grass"></div><div class="share"><span></span><span></span><span></span></div><h4>Numquam modi tempora incidunt</h4><p>At vloreero eos et accusamuos et accusamuss dilo rsocimuupiditate non provident...</p><div class="meta"><span>20 FEB 2019</span><span>|</span><span>Comments (05)</span></div></article>
    <article class="post"><div class="thumb b2" role="img" aria-label="Players contesting the ball in a match"></div><div class="share"><span></span><span></span><span></span></div><h4>Numquam modi tempora incidunt</h4><p>At vloreero eos et accusamuos et accusamuss dilo rsocimuupiditate non provident...</p><div class="meta"><span>20 FEB 2019</span><span>|</span><span>Comments (05)</span></div></article>
    <article class="post"><div class="thumb b3" role="img" aria-label="Players in a floodlit stadium at night"></div><div class="share"><span></span><span></span><span></span></div><h4>Numquam modi tempora incidunt</h4><p>At vloreero eos et accusamuos et accusamuss dilo rsocimuupiditate non provident...</p><div class="meta"><span>20 FEB 2019</span><span>|</span><span>Comments (05)</span></div></article>
  </div>
</section>

<section class="map">
  <div class="map-fill" role="img" aria-label="Street map showing the office location"></div>
  <svg class="pin" width="26" height="36" viewBox="0 0 26 36"><path d="M13 0C6 0 0 5.6 0 12.6 0 22 13 36 13 36s13-14 13-23.4C26 5.6 20 0 13 0z" fill="#e0332b"/><circle cx="13" cy="12.5" r="4.5" fill="#8d1a14"/></svg>
  <div class="map-card">1420 Harlow Lane,<br>Suite B, Austin,<br>TX 78701</div>
</section>

<footer class="footer">
  <span class="brand">CRESTGUARD</span>
  <div class="social"><span></span><span></span><span></span><span></span><span></span></div>
  <p class="copy">Copyrights © 2020 The Company Name. All Rights Reserved.</p>
</footer>

</body>
</html>
```